Heron Loan Partners Business Card

We need a business card design for our mortgage servicing company. In addition to servicing the loans of homeowners, we help homeowners with purchasing their homes and any mortgage refinancing. We would like to see designs that use the colors in the logo attached below (gold-ish yellow and navy blue), and any other design you deem fit! The design should communicate a simpler life with smart mortgages provided by Heron.

```html
<!DOCTYPE html>
<html lang="en">
<head>
<meta charset="utf-8">
<title>Heron Loan Partners Business Card</title>
<link href="https://fonts.googleapis.com/css2?family=Open+Sans:wght@400;600;700&display=swap" rel="stylesheet">
<style>
  :root {
    --bg: #d6d6d6;
    --paper: #f3f3f4;
    --gold: #d6a21c;
    --navy: #1d1b5c;
    --ink: #1e1e24;
  }
  * { box-sizing: border-box; margin: 0; padding: 0; }
  html, body { width: 1200px; height: 1051px; overflow: hidden; }
  body {
    background: var(--bg);
    font-family: "Open Sans", Arial, sans-serif;
    color: var(--ink);
    position: relative;
  }
  .card {
    position: absolute;
    left: 200px;
    width: 800px;
    height: 457px;
    background: var(--paper);
    border-bottom: 5px solid var(--gold);
    box-shadow: 0 18px 40px rgba(0,0,0,0.18);
  }
  .card--back { top: 48px; }
  .card--front { top: 544px; }

  .wordmark {
    position: absolute;
    display: flex;
    align-items: center;
    gap: 16px;
    white-space: nowrap;
  }
  .wordmark__dot {
    flex: none;
    width: 26px; height: 26px;
    border-radius: 50%;
    background: var(--navy);
  }
  .wordmark__name {
    font-weight: 700;
    color: var(--gold);
    letter-spacing: 0.5px;
    line-height: 1.1;
  }
  .card--back .wordmark { left: 50%; top: 50%; transform: translate(-50%, -50%); }
  .card--back .wordmark__name { font-size: 64px; }
  .card--back .wordmark__dot { width: 40px; height: 40px; }

  .card--front .wordmark { right: 90px; top: 78px; }
  .card--front .wordmark__name { font-size: 44px; }

  .person { position: absolute; left: 60px; top: 70px; }
  .person__name {
    font-weight: 700;
    font-size: 30px;
    color: var(--gold);
    letter-spacing: 0.5px;
    text-transform: uppercase;
  }
  .person__title { font-size: 20px; margin-top: 2px; }

  .divider {
    position: absolute;
    left: 60px; right: 60px; top: 160px;
    height: 2px;
    background: var(--gold);
  }

  .contacts {
    position: absolute;
    left: 60px; top: 182px;
    list-style: none;
    font-size: 20px;
    line-height: 34px;
  }
  .contacts li { display: flex; align-items: center; gap: 12px; }
  .contacts svg { width: 16px; height: 16px; fill: var(--gold); flex: none; }

  .address {
    position: absolute;
    right: 60px; bottom: 50px;
    text-align: right;
    font-size: 20px;
    line-height: 30px;
  }
</style>
</head>
<body>
  <section class="card card--back" aria-label="Card back">
    <div class="wordmark">
      <span class="wordmark__dot"></span>
      <span class="wordmark__name">Heron Loan Partners</span>
    </div>
  </section>

  <section class="card card--front" aria-label="Card front">
    <div class="person">
      <p class="person__name">Dana Whitfield</p>
      <p class="person__title">Managing Director</p>
    </div>

    <div class="wordmark">
      <span class="wordmark__dot"></span>
      <span class="wordmark__name">Heron</span>
    </div>

    <div class="divider"></div>

    <ul class="contacts">
      <li>
        <svg viewBox="0 0 16 16" aria-hidden="true"><path d="M3.5 1l2.5 3-1.5 1.8c.9 2 2.3 3.4 4.2 4.2L10.5 8.5l3 2.5-1.4 2.6C7 13.5 2.5 9 2.4 3.9z"/></svg>
        123 456 789
      </li>
      <li>
        <svg viewBox="0 0 16 16" aria-hidden="true"><path d="M1 3h14v10H1z M1 3l7 6 7-6" fill-rule="evenodd"/></svg>
        info@yourgmail.com
      </li>
      <li>
        <svg viewBox="0 0 16 16" aria-hidden="true"><circle cx="8" cy="8" r="7"/></svg>
        www.yourwebsite.com
      </li>
    </ul>

    <p class="address">Your address, City<br>State, Zip 1234</p>
  </section>
</body>
</html>
```